Healthcare/Medical Consultant Company

QRN is a Healthcare Conultant Company. We help doctors manage the business side of their medical practice.
We already have a very basic world press design. We want an upgraded design that conveys partnership, healthcare expertise and healthcare innovation to our client. It needs to have a sleek, clean, modern and inclusive look. Pictures need need to convey diversity (including pictures of people of all races and shows both men and women working together in a healthcare environment to make it better). The Pictures on the home page should particularly illustrate diversity and Healthcare expertise. The company logo is blue and white but the site doesn’t have to follow the exact same theme but the logo needs to blend well with the chosen theme. The logo should ideally be in the header of the website. We would also like the following included in our website:

1. Pages should include: a home page, About Us page, Services page, Get a quote page, Contact Us page, Staff page(where we can add pictures and bio for staff).

2. The Drop down menu for services should have hyperlinks ( for each service)Leading to a page that provides detailed info about that specific service. Our services include: Revenue Cycle Management, Regulatory Compliance, Human Resources Management, & practice Management.

3. Links to social media should in the header or footer of each page.

4. Contact info should be in the footer of each page.

5. Clients should be an email to us from the contact page.

Target Market(s)

Physician Medical Practices

Industry/Entity Type

Medical

Coding

Coded - Design and coding required

Font styles to use
Sans Serif

Colors

Designer to choose colors to be used in the design.

Requirements
Must have
• See project description
Nice to have
• See project description

```html
<!DOCTYPE html>
<html lang="en">
<head>
<meta charset="utf-8">
<title>QRN Health Partners</title>
<link href="https://fonts.googleapis.com/css2?family=Cinzel:wght@400;700&family=Oswald:wght@500;600&family=Montserrat:wght@400;500;600&display=swap" rel="stylesheet">
<style>
:root{
  --navy:#0b4f9c;
  --navy-dark:#0a4586;
  --sky:#35a4db;
  --sky-light:#5fb8e4;
  --text:#555;
  --white:#fff;
}
*{margin:0;padding:0;box-sizing:border-box}
html,body{width:1200px;height:3475px;overflow:hidden}
body{position:relative;font-family:"Montserrat",sans-serif;color:var(--text);background:var(--white)}
section,header,footer{position:absolute;left:0;width:1200px}
.serif{font-family:"Cinzel",serif}

/* wordmark: plain company name in the body font */
.wordmark{font-family:"Montserrat",sans-serif;font-weight:600;color:var(--navy);line-height:1;letter-spacing:1px}

/* header */
.site-header{top:0;height:120px;background:var(--white)}
.brand{position:absolute;left:78px;top:30px;display:flex;align-items:center;gap:14px}
.brand .wordmark{font-size:40px}
.brand-full{font-family:"Montserrat",sans-serif;font-size:13px;font-weight:500;color:#333;width:140px;line-height:1.35}
.topbar{position:absolute;right:0;top:0;height:52px;display:flex;align-items:center;gap:14px}
.social{display:flex;gap:8px}
.social span{width:30px;height:30px;border-radius:50%;border:2px solid var(--navy);display:block}
.phone-pill{background:var(--sky);color:var(--white);height:52px;padding:0 32px 0 22px;display:flex;align-items:center;gap:10px;font-size:22px;border-radius:0 0 0 10px}
.main-nav{position:absolute;right:70px;top:76px;display:flex;gap:28px;font-size:15px;font-weight:500;color:#222;align-items:center}
.main-nav .active{color:var(--sky)}

/* hero */
.hero{top:120px;height:547px;background:linear-gradient(120deg,#cfd8e0,#e9eef1 40%,#b9c7d4 75%,#8aa0b5)}
.hero-card{position:absolute;left:79px;top:158px;width:480px;height:285px;background:rgba(255,255,255,.88);padding:30px}
.hero-card h1{font-family:"Oswald",sans-serif;font-weight:600;font-size:40px;color:var(--navy);letter-spacing:1px;line-height:1}
.hero-card h2{font-size:18px;font-weight:600;color:#222;margin:12px 0 14px}
.hero-card p{font-size:14px;line-height:1.75}
.btn{display:inline-block;font-family:"Cinzel",serif;font-size:18px;padding:12px 26px;border-radius:6px}
.btn-sky{background:var(--sky);color:var(--white);margin-top:14px}
.btn-white{background:var(--white);color:var(--navy)}

/* band */
.solution-band{top:667px;height:179px;background:var(--sky);color:var(--white)}
.solution-band h2{position:absolute;left:79px;top:44px;font-size:30px;font-weight:400}
.solution-band p{position:absolute;left:79px;top:90px;width:720px;font-size:13px;line-height:1.8}
.solution-band .btn{position:absolute;right:78px;top:62px}

/* welcome */
.welcome{top:846px;height:482px}
.welcome h2{position:absolute;left:79px;top:54px;font-size:44px;color:var(--navy);font-weight:400}
.welcome .copy{position:absolute;left:79px;top:120px;width:580px;font-size:13px;line-height:2}
.welcome .copy p{margin-bottom:14px}
.welcome .copy strong{font-weight:500;color:#222;font-size:14px}
.welcome .btn{position:absolute;left:79px;top:366px;margin:0}
.welcome-photo{position:absolute;left:728px;top:60px;width:396px;height:359px;background:linear-gradient(160deg,#dfe8ee,#b8c8d4 60%,#7f96a8)}

/* services */
.services{top:1328px;height:678px;background:radial-gradient(circle at 50% 40%,#2a72b8,#0d4f9a 60%,#0a4384);overflow:hidden}
.services h2{position:absolute;top:50px;width:100%;text-align:center;font-size:40px;color:var(--white);font-weight:400}
.services h2 span{color:var(--sky-light)}
.hub{position:absolute;left:396px;top:321px;width:408px;height:408px;border-radius:50%;background:var(--white);display:flex;justify-content:center;padding-top:150px}
.hub .wordmark{font-size:72px}
.service{position:absolute;width:220px;text-align:center;color:var(--white);font-family:"Cinzel",serif;font-size:16px;line-height:1.3}
.service .icon{width:120px;height:120px;border-radius:50%;background:var(--sky);margin:0 auto 12px;border:4px solid rgba(255,255,255,.25);display:flex;align-items:center;justify-content:center}
.service .icon.dark{background:#0f4c93;border-color:#5fb8e4}

/* quote */
.quote{top:2006px;height:418px;background:var(--sky);color:var(--white);text-align:center}
.quote h2{font-size:42px;font-weight:400;margin-top:50px}
.quote h2 span{color:var(--navy)}
.quote p{width:760px;margin:14px auto 0;font-size:14px;line-height:1.9}
.quote-form{position:absolute;left:155px;top:194px;width:892px;display:grid;grid-template-columns:290px 290px 290px;grid-template-rows:46px 46px;gap:10px 11px}
.field{background:rgba(255,255,255,.25);border:1px solid rgba(255,255,255,.35);font-size:12px;text-align:left;padding:14px 10px;color:#e8f5fc}
.field.tall{grid-row:1/3;grid-column:3}
.quote .btn{position:absolute;left:524px;top:305px;width:152px;padding:12px 0;font-size:18px;letter-spacing:1px}

/* staff */
.staff{top:2424px;height:600px;text-align:center}
.staff h2{font-size:42px;color:var(--sky);font-weight:400;margin-top:54px}
.staff h2 span{color:var(--navy)}
.staff > p{width:760px;margin:14px auto 0;font-size:14px;line-height:1.9}
.card{position:absolute;top:198px;width:302px;height:332px;background:var(--white);box-shadow:0 2px 10px rgba(0,0,0,.15)}
.card .photo{height:250px;background:linear-gradient(160deg,#eef1f3,#cfd8df)}
.card h3{font-size:18px;font-weight:600;color:var(--navy);margin-top:20px}
.card a{font-family:"Cinzel",serif;font-size:15px;color:var(--sky)}
.card.featured .meta{background:var(--navy);height:82px;padding-top:1px}
.card.featured h3{color:var(--white)}
.card.featured a{color:#9cc7ec}

/* contact band */
.contact-band{top:3024px;height:123px;background:var(--sky);display:flex;align-items:center;justify-content:center;gap:28px;color:var(--white);font-size:18px;font-weight:500}

/* footer */
.site-footer{top:3147px;height:328px;background:var(--navy);color:var(--white)}
.footer-brand{position:absolute;left:88px;top:72px;width:240px;text-align:center}
.footer-brand .wordmark{color:var(--white);font-size:56px;display:block}
.footer-brand .social{justify-content:center;margin-top:36px}
.footer-brand .social span{width:40px;height:40px;background:var(--sky);border:none}
.col{position:absolute;top:40px;font-size:13px}
.col h4{font-family:"Cinzel",serif;font-size:17px;font-weight:400;margin-bottom:16px}
.col li{list-style:none;line-height:29px;padding-left:16px;position:relative}
.col li::before{content:"";position:absolute;left:0;top:11px;border:4px solid transparent;border-left-color:var(--sky-light)}
.contact-row{display:flex;gap:16px;margin-bottom:18px;line-height:1.7}
.contact-row svg{flex:none;margin-top:2px}
.copyright{position:absolute;left:0;bottom:0;width:100%;height:57px;background:var(--navy-dark);border-top:1px solid rgba(255,255,255,.15);text-align:center;line-height:57px;font-size:13px}
</style>
</head>
<body>

<header class="site-header">
  <div class="brand"><span class="wordmark">QRN</span><span class="brand-full">QRN Health Partners LLC</span></div>
  <div class="topbar">
    <div class="social"><span></span><span></span><span></span></div>
    <div class="phone-pill">
      <svg width="20" height="20" viewBox="0 0 24 24"><path fill="#fff" d="M6.6 10.8a15 15 0 006.6 6.6l2.2-2.2c.3-.3.7-.4 1-.2 1.1.4 2.3.6 3.6.6.6 0 1 .4 1 1V20c0 .6-.4 1-1 1A17 17 0 013 4c0-.6.4-1 1-1h3.5c.6 0 1 .4 1 1 0 1.3.2 2.5.6 3.6.1.3 0 .7-.2 1z"/></svg>
      123 456 7890
    </div>
  </div>
  <nav class="main-nav">
    <span class="active">HOME ▾</span><span>ABOUT US</span><span>SERVICES</span><span>GET A QUOTE</span><span>CONTACT US</span><span>STAFF</span>
    <svg width="16" height="16" viewBox="0 0 24 24"><circle cx="10" cy="10" r="7" fill="none" stroke="#222" stroke-width="3"/><path d="M15 15l7 7" stroke="#222" stroke-width="3"/></svg>
  </nav>
</header>

<section class="hero" role="img" aria-label="Diverse team of doctors and nurses working together at a table">
  <div class="hero-card">
    <h1>HEALTHCARE CONULTANT</h1>
    <h2>QRN Health Partners</h2>
    <p>Lorem Ipsum is simply dummy text of the printing and typesetting industry. Lorem Ipsum has been the industry's standard dummy text ever since the.</p>
    <span class="btn btn-sky">READ MORE</span>
  </div>
</section>

<section class="solution-band">
  <h2 class="serif">Providing Toatl Health Care Solution</h2>
  <p>Lorem Ipsum is simply dummy text of the printing and typesetting industry. Lorem Ipsum has been the industry's standard dummy text ever since the.</p>
  <span class="btn btn-white">GET AN APPOINTMENT</span>
</section>

<section class="welcome">
  <h2 class="serif">Welcome To QRN</h2>
  <div class="copy">
    <p>Lorem Ipsum is simply dummy text of the printing and typesetting industry. Lorem Ipsum has been the industry's standard dummy text ever since the when an unknown a galley of type and scrambled it to mak</p>
    <p>Lorem Ipsum is simply dummy text of the printing and typesetting industry. Lorem Ipsum has been the industry's standard dummy text ever since the, when an unknown printer took a galley of type and scrambled it to mak Lorem Ipsum is simply dummy text of the printing and typesetting industry.</p>
    <strong>Lorem Ipsum has been the industry's standard dummy text ever.</strong>
  </div>
  <span class="btn btn-sky">LEARN MORE</span>
  <div class="welcome-photo" role="img" aria-label="Medical staff walking down a bright hospital corridor"></div>
</section>

<section class="services" aria-label="Our services">
  <h2 class="serif"><span>Our</span> Services</h2>
  <div class="hub"><span class="wordmark">QRN</span></div>
  <div class="service" style="left:490px;top:140px">
    <div class="icon"><svg width="56" height="56" viewBox="0 0 24 24" fill="none" stroke="#fff" stroke-width="1.5"><circle cx="12" cy="12" r="3.5"/><path d="M12 2v3M12 19v3M2 12h3M19 12h3M4.9 4.9l2.1 2.1M17 17l2.1 2.1M4.9 19.1L7 17M17 7l2.1-2.1"/></svg></div>
    Regulatory<br>Compliance
  </div>
  <div class="service" style="left:252px;top:232px">
    <div class="icon"><svg width="52" height="52" viewBox="0 0 24 24" fill="none" stroke="#fff" stroke-width="1.5"><rect x="5" y="4" width="14" height="18" rx="1"/><rect x="9" y="2" width="6" height="4"/><path d="M8 11h8M8 14h8M8 17h5"/></svg></div>
    Medical Billing<br>&amp; Coding
  </div>
  <div class="service" style="left:740px;top:232px">
    <div class="icon"><svg width="52" height="52" viewBox="0 0 24 24" fill="none" stroke="#fff" stroke-width="1.5"><rect x="3" y="4" width="18" height="12"/><path d="M9 20h6M12 16v4"/><circle cx="10" cy="9" r="2"/><path d="M7 14c0-2 6-2 6 0"/></svg></div>
    Human Resources<br>Training
  </div>
  <div class="service" style="left:107px;top:435px">
    <div class="icon dark"><svg width="52" height="52" viewBox="0 0 24 24" fill="none" stroke="#fff" stroke-width="1.5"><circle cx="9" cy="9" r="6"/><path d="M14 15h7M14 18h7M14 21h7M9 6v6"/></svg></div>
    Revenue Cycle<br>Management
  </div>
  <div class="service" style="left:858px;top:435px">
    <div class="icon"><svg width="52" height="52" viewBox="0 0 24 24" fill="none" stroke="#fff" stroke-width="1.5"><rect x="3" y="3" width="18" height="13"/><path d="M6 12l4-4 3 3 5-5M8 20h8"/></svg></div>
    Staff Education &amp;<br>Training
  </div>
</section>

<section class="quote">
  <h2 class="serif">Get A <span>Quote</span></h2>
  <p>Lorem Ipsum is simply dummy text of the printing and typesetting industry. Lorem Ipsum has been the industry's standard dummy text ever since the.</p>
  <div class="quote-form">
    <div class="field">Name *</div>
    <div class="field">Serices *</div>
    <div class="field tall">Your Query *</div>
    <div class="field">Email*</div>
    <div class="field">Phone *</div>
  </div>
  <span class="btn btn-white">SUBMIT</span>
</section>

<section class="staff">
  <h2 class="serif">Meet Our <span>Staff</span></h2>
  <p>Lorem Ipsum is simply dummy text of the printing and typesetting industry. Lorem Ipsum has been the industry's standard dummy text ever since the.</p>
  <div class="card" style="left:116px"><div class="photo" role="img" aria-label="Portrait of a senior male doctor"></div><div class="meta"><h3>MEMBER NAME</h3><a>View Bio</a></div></div>
  <div class="card featured" style="left:449px"><div class="photo" role="img" aria-label="Portrait of a male doctor holding a tablet"></div><div class="meta"><h3>MEMBER NAME</h3><a>View Bio</a></div></div>
  <div class="card" style="left:783px"><div class="photo" role="img" aria-label="Portrait of a young male doctor"></div><div class="meta"><h3>MEMBER NAME</h3><a>View Bio</a></div></div>
</section>

<section class="contact-band">
  <span>If You Need An Have Question Please Contact Us.</span>
  <span class="btn btn-white">GET AN APPOINTMENT</span>
</section>

<footer class="site-footer">
  <div class="footer-brand">
    <span class="wordmark">QRN</span>
    <div class="social"><span></span><span></span><span></span></div>
  </div>
  <div class="col" style="left:345px"><h4>Sitemap</h4><ul><li>Home</li><li>About Us</li><li>Services</li><li>Get a Quote</li><li>Contact Us</li><li>Staff</li></ul></div>
  <div class="col" style="left:610px"><h4>Services</h4><ul><li>Revenue Cycle Management</li><li>Medical Billing &amp; Coding</li><li>Regulatory Compliance</li><li>Human Resources Training</li><li>Staff Education and Training</li></ul></div>
  <div class="col" style="left:873px;width:250px"><h4>Contact Us</h4>
    <div class="contact-row"><svg width="20" height="26" viewBox="0 0 20 26"><path fill="#5fb8e4" d="M10 0a9 9 0 00-9 9c0 7 9 17 9 17s9-10 9-17a9 9 0 00-9-9zm0 13a4 4 0 110-8 4 4 0 010 8z"/></svg><span>101 - Lorem ipsum is simple dummy text of print.</span></div>
    <div class="contact-row"><svg width="20" height="20" viewBox="0 0 24 24"><path fill="#5fb8e4" d="M6.6 10.8a15 15 0 006.6 6.6l2.2-2.2c.3-.3.7-.4 1-.2 1.1.4 2.3.6 3.6.6.6 0 1 .4 1 1V20c0 .6-.4 1-1 1A17 17 0 013 4c0-.6.4-1 1-1h3.5c.6 0 1 .4 1 1 0 1.3.2 2.5.6 3.6.1.3 0 .7-.2 1z"/></svg><span>123 456 7890</span></div>
    <div class="contact-row"><svg width="20" height="16" viewBox="0 0 20 16"><rect width="20" height="16" fill="#5fb8e4"/><path d="M0 0l10 8 10-8" fill="none" stroke="#0b4f9c" stroke-width="1.5"/></svg><span>info@QRN.com</span></div>
  </div>
  <div class="copyright">©QRN - 2018 All Right Reserved.</div>
</footer>

</body>
</html>
```